Unusual Options Activity Graphic Card Design for Finance App

We are developing a financial data platform called Vantix Pulse, and we need a visually striking, mobile-optimized graphic card design to display unusual options activity. The card will be featured in our mobile app and marketing materials, inspired by platforms like Quorafin and Marlow Tide.
🔹 Design Goals:
Modern, clean, and professional aesthetic
Use vibrant electric blue, green, or dark theme gradients
Must feel tech-savvy and finance-oriented
Layout should be optimized for vertical mobile format (portrait)
🔹 Information to Include in the Card:
Ticker Symbol (e.g., QRV) with colored badge
Date & Time of trade
Trade Type (e.g., Sweep Call / Put)
Execution Type (At Ask or At Bid)
Strike Price
Expiration Date
Premium (e.g., $342.75K)
Size@Price (e.g., 6995@$0.49)
Volume
Open Interest
Branding at bottom: “Vantix Pulse” in modern font
🔹 Inspiration:
Quorafin’s profit/loss cards
Clean fintech dashboards (Sparvane, Marlow Tide, Kestrowe Console)
Please provide the final deliverable in high-resolution PNG and layered PSD or Figma file for future edits.
Stock Market Traders
Finance

```html
<!DOCTYPE html>
<html lang="en">
<head>
<meta charset="utf-8">
<title>Unusual Options Activity : Graphic Card Design for Finance App</title>
<link rel="stylesheet" href="https://fonts.googleapis.com/css2?family=Inter:wght@400;500;600;700;800;900&display=swap">
<style>
  :root{
    --board:#050914;
    --phone:#000000;
    --white:#ffffff;
    --muted:#a9b3c7;
    --green:#4ed07a;
    --green-badge:#5cc56a;
    --red-badge:#e04848;
    --red:#ff4d4d;
    --ink:#08140c;
    --line:rgba(255,255,255,.22);
    --tab-line:#2a2d33;
    --navy-1:#1c2c4d;
    --navy-2:#15377f;
  }
  *{box-sizing:border-box;margin:0;padding:0}
  html,body{width:1200px;height:1109px;overflow:hidden;background:var(--board)}
  body{font-family:"Inter",sans-serif;color:var(--white)}
  .board{position:absolute;left:0;top:0;width:2000px;height:1848px;transform:scale(.6);transform-origin:0 0;background:var(--board)}

  .headline{position:absolute;left:0;width:1928px;top:70px;text-align:center;font-size:48px;font-weight:800;letter-spacing:-1.2px;line-height:58px}
  .step{position:absolute;top:470px;width:200px;text-align:center;font-size:92px;font-weight:800;line-height:100px}

  .phone{position:absolute;top:607px;width:382px;height:828px;background:var(--phone);border-radius:20px;overflow:hidden}
  .status{position:absolute;left:0;right:0;top:16px;height:22px}
  .status .clock{position:absolute;left:47px;top:0;font-size:15px;font-weight:600;line-height:22px}
  .status svg{position:absolute;top:4px}
  .screen-title{position:absolute;left:0;right:0;top:56px;text-align:center;font-size:18px;line-height:24px}
  .tabs{position:absolute;top:94px;left:0;right:0;height:31px;border-bottom:2px solid var(--tab-line)}
  .tab{position:absolute;top:0;font-size:12px;line-height:16px;font-weight:500}
  .tab.active{color:var(--green)}
  .tab.active::after{content:"";position:absolute;left:0;right:0;top:27px;height:3px;background:var(--green)}
  .feed{position:absolute;top:126px;left:0;right:0;height:622px;overflow:hidden}
  .navbar{position:absolute;left:0;right:0;top:748px;height:80px}
  .nav-item{position:absolute;top:14px;width:40px;margin-left:-20px;text-align:center}
  .nav-item svg{display:block;margin:0 auto}
  .nav-item.active{color:var(--green);font-size:12px}
  .home-bar{position:absolute;left:122px;top:817px;width:138px;height:4px;border-radius:2px;background:var(--white)}

  .card{position:absolute;border-radius:14px;overflow:hidden}
  .card-blue{left:41px;width:300px;background:linear-gradient(180deg,#1e2b48 0%,#18306b 55%,#163b8e 100%)}
  .card-deep{left:40px;width:300px;background:linear-gradient(160deg,#111a30 0%,#132650 55%,#163175 100%)}
  .card-aurora{left:40px;width:300px;background:radial-gradient(140% 90% at 0% 0%,#21513d 0%,#163a4a 40%,#112a68 100%)}
  .card-moss{left:43px;width:295px;background:linear-gradient(150deg,#2b5a47 0%,#22483f 50%,#1f3d3e 100%)}

  .ticker-badge{position:absolute;display:flex;align-items:stretch;height:32px;border:1.5px solid rgba(255,255,255,.85);border-radius:4px;overflow:hidden}
  .ticker-badge .ticker{width:56px;background:var(--green-badge);color:var(--ink);font-weight:800;font-size:16px;display:flex;align-items:center;justify-content:center}
  .ticker-badge.bearish .ticker{background:var(--red-badge);color:var(--white)}
  .ticker-badge .stamp{padding:0 14px 0 12px;font-size:17px;display:flex;align-items:center;white-space:nowrap}

  .trade-type{position:absolute;font-weight:900;letter-spacing:.5px;white-space:nowrap}
  .trade-type .side{color:var(--green)}
  .execution{position:absolute;font-size:17px;line-height:20px;color:var(--green)}
  .execution.plain{color:var(--muted);font-size:15px}

  .stats{position:absolute;display:grid;grid-template-columns:124px 124px;row-gap:8px}
  .stat .label{font-size:12px;line-height:16px;color:var(--muted);letter-spacing:.3px}
  .stat .value{font-size:18px;line-height:24px;font-weight:700;margin-top:2px}

  .mini-stats{position:absolute;left:21px;top:97px;display:grid;grid-template-columns:83px 96px 90px;row-gap:6px}
  .mini-stats .label{font-size:8px;line-height:11px;color:#b8c6c0;letter-spacing:.3px}
  .mini-stats .value{font-size:12px;line-height:16px;font-weight:700}

  .divider{position:absolute;height:1px;background:var(--line)}
  .brand{position:absolute;display:flex;align-items:center;gap:8px;font-weight:800;white-space:nowrap;color:var(--white)}
  .brand .dot{border-radius:50%;background:var(--green);flex:none}

  .poster{position:absolute;left:28px;top:28px;font-weight:900;line-height:1}
  .poster .big{font-size:48px;letter-spacing:.5px}
  .poster .sub{font-size:24px;font-weight:800;margin-top:6px;letter-spacing:.4px}
  .author{position:absolute;left:20px;top:436px;display:flex;align-items:center;gap:9px}
  .author .avatar{width:38px;height:38px;border-radius:50%;background:radial-gradient(circle at 50% 45%,#d9dde3 0%,#8a929e 70%,#4b5261 100%)}
  .author .name{font-size:12px;font-weight:700}
  .author .when{font-size:10px;color:var(--muted);margin-top:6px}

  .thanks{position:absolute;left:0;right:0;top:1578px;text-align:center;font-size:104px;font-weight:800;letter-spacing:-4px;line-height:120px}
  .thanks-note{position:absolute;left:0;right:0;top:1710px;text-align:center;font-size:36px;line-height:46px;font-weight:400}
</style>
</head>
<body>
<main class="board">
  <h1 class="headline">Unusual Options Activity&nbsp; :&nbsp; Graphic Card<br>Design for Finance App</h1>

  <div class="step" style="left:220px">1</div>
  <div class="step" style="left:655px">2</div>
  <div class="step" style="left:1128px">3</div>
  <div class="step" style="left:1610px">4</div>

  <!-- Screen 1 -->
  <section class="phone" style="left:125px">
    <div class="status"><span class="clock">7:09 &#9679;</span>
      <svg style="left:270px" width="80" height="14" viewBox="0 0 80 14" fill="#fff"><rect x="0" y="9" width="3" height="4"/><rect x="5" y="6" width="3" height="7"/><rect x="10" y="3" width="3" height="10"/><rect x="15" y="0" width="3" height="13"/><path d="M26 5a10 10 0 0 1 14 0l-2 2a7 7 0 0 0-10 0zM29 8a5 5 0 0 1 8 0l-4 4z"/><rect x="50" y="1" width="23" height="11" rx="3"/><rect x="74" y="4" width="2" height="5" rx="1"/></svg>
    </div>
    <div class="screen-title">Markets</div>
    <nav class="tabs"><span class="tab active" style="left:13px">Option Flow</span><span class="tab" style="left:112px">Darkpool</span><span class="tab" style="left:193px">Treemap</span><span class="tab" style="left:273px">Gamma</span><span class="tab" style="left:346px">Snaps</span></nav>
    <div class="feed">
      <article class="card card-blue" style="top:35px;height:446px">
        <div class="ticker-badge" style="left:24px;top:21px"><span class="ticker">HVL</span><span class="stamp">04/05/25 | 10:32:12</span></div>
        <div class="trade-type" style="left:24px;top:72px;font-size:38px;line-height:46px">SWEEP <span class="side">CALL</span></div>
        <div class="execution plain" style="left:24px;top:120px">AT ASk</div>
        <svg style="position:absolute;left:24px;top:135px" width="254" height="84" viewBox="0 0 254 84">
          <defs><linearGradient id="chartFill" x1="0" y1="0" x2="0" y2="1"><stop offset="0" stop-color="#4ed07a" stop-opacity=".7"/><stop offset="1" stop-color="#4ed07a" stop-opacity="0"/></linearGradient></defs>
          <path d="M0 78 L8 70 L14 74 L22 64 L28 68 L36 60 L42 66 L50 58 L56 62 L64 52 L70 58 L78 50 L84 56 L92 44 L98 52 L106 46 L112 50 L120 40 L126 46 L134 38 L140 44 L148 30 L156 40 L164 34 L172 38 L180 26 L188 32 L196 20 L204 28 L212 16 L220 24 L228 12 L236 18 L244 8 L250 2 L252 30 L252 84 L0 84 Z" fill="url(#chartFill)"/>
          <path d="M0 78 L8 70 L14 74 L22 64 L28 68 L36 60 L42 66 L50 58 L56 62 L64 52 L70 58 L78 50 L84 56 L92 44 L98 52 L106 46 L112 50 L120 40 L126 46 L134 38 L140 44 L148 30 L156 40 L164 34 L172 38 L180 26 L188 32 L196 20 L204 28 L212 16 L220 24 L228 12 L236 18 L244 8 L250 2" fill="none" stroke="#6ee28f" stroke-width="2"/>
        </svg>
        <div class="stats" style="left:24px;top:230px">
          <div class="stat"><div class="label">STRIKE</div><div class="value">$91</div></div>
          <div class="stat"><div class="label">EXPIRATION</div><div class="value">19 Apr 25</div></div>
          <div class="stat"><div class="label">PREMIUM</div><div class="value">$342.75K</div></div>
          <div class="stat"><div class="label">SIZE@PRICE</div><div class="value">6995@$0.49</div></div>
          <div class="stat"><div class="label">VOLUME</div><div class="value">34.7K</div></div>
          <div class="stat"><div class="label">OPEN INTEREST</div><div class="value">2424</div></div>
        </div>
        <div class="divider" style="left:24px;right:24px;top:386px"></div>
        <div class="brand" style="left:70px;top:398px;font-size:18px"><span class="dot" style="width:22px;height:22px"></span>Vantix Pulse</div>
      </article>
      <article class="card card-blue" style="top:505px;height:300px">
        <div class="ticker-badge" style="left:24px;top:21px"><span class="ticker">HVL</span><span class="stamp">04/05/25 | 10:32:12</span></div>
        <div class="trade-type" style="left:24px;top:72px;font-size:38px;line-height:46px">SWEEP <span class="side">CALL</span></div>
      </article>
    </div>
    <div class="navbar">
      <div class="nav-item" style="left:32px"><svg width="18" height="18" viewBox="0 0 18 18" fill="#fff"><rect x="1" y="1" width="7" height="9"/><rect x="10" y="1" width="7" height="5"/><rect x="1" y="12" width="7" height="5"/><rect x="10" y="8" width="7" height="9"/></svg></div>
      <div class="nav-item" style="left:103px"><svg width="18" height="18" viewBox="0 0 18 18" fill="#fff"><path d="M3 1h9l4 4v12H3z"/><rect x="6" y="8" width="7" height="1.5" fill="#000"/><rect x="6" y="11" width="7" height="1.5" fill="#000"/></svg></div>
      <div class="nav-item active" style="left:190px;width:70px;margin-left:-35px"><svg width="18" height="12" viewBox="0 0 18 12" fill="none" stroke="#4ed07a" stroke-width="2"><path d="M1 11l5-5 3 3 7-7M12 2h4v4"/></svg>Markets</div>
      <div class="nav-item" style="left:278px"><svg width="18" height="18" viewBox="0 0 18 18" fill="#fff"><rect x="2" y="8" width="3.5" height="9"/><rect x="7.5" y="2" width="3.5" height="15"/><rect x="13" y="10" width="3.5" height="7"/></svg></div>
      <div class="nav-item" style="left:348px"><svg width="18" height="18" viewBox="0 0 18 18" fill="#fff"><circle cx="9" cy="5" r="4"/><path d="M1 17c0-5 4-7 8-7s8 2 8 7z"/></svg></div>
    </div>
    <div class="home-bar"></div>
  </section>

  <!-- Screen 2 -->
  <section class="phone" style="left:581px">
    <div class="status"><span class="clock">7:09 &#9679;</span>
      <svg style="left:270px" width="80" height="14" viewBox="0 0 80 14" fill="#fff"><rect x="0" y="9" width="3" height="4"/><rect x="5" y="6" width="3" height="7"/><rect x="10" y="3" width="3" height="10"/><rect x="15" y="0" width="3" height="13"/><path d="M26 5a10 10 0 0 1 14 0l-2 2a7 7 0 0 0-10 0zM29 8a5 5 0 0 1 8 0l-4 4z"/><rect x="50" y="1" width="23" height="11" rx="3"/><rect x="74" y="4" width="2" height="5" rx="1"/></svg>
    </div>
    <div class="screen-title">Markets</div>
    <nav class="tabs"><span class="tab active" style="left:13px">Option Flow</span><span class="tab" style="left:112px">Darkpool</span><span class="tab" style="left:193px">Treemap</span><span class="tab" style="left:273px">Gamma</span><span class="tab" style="left:346px">Snaps</span></nav>
    <div class="feed">
      <article class="card card-deep" style="top:19px;height:498px">
        <div class="poster"><div class="big">UNUSUAL</div><div class="sub">OPTIONS ACTIVITY</div></div>
        <div class="ticker-badge" style="left:28px;top:119px"><span class="ticker">HVL</span><span class="stamp">04/05/25 | 10:32:12</span></div>
        <div class="trade-type" style="left:28px;top:167px;font-size:38px;line-height:46px">TRADE <span class="side">CALL</span></div>
        <div class="execution" style="left:28px;top:216px">AT ASk</div>
        <div class="stats" style="left:28px;top:253px">
          <div class="stat"><div class="label">STRIKE</div><div class="value">$91</div></div>
          <div class="stat"><div class="label">EXPIRATION</div><div class="value">19 Apr 25</div></div>
          <div class="stat"><div class="label">PREMIUM</div><div class="value">$342.75K</div></div>
          <div class="stat"><div class="label">SIZE@PRICE</div><div class="value">6995@$0.49</div></div>
          <div class="stat"><div class="label">VOLUME</div><div class="value">34.7K</div></div>
          <div class="stat"><div class="label">OPEN INTEREST</div><div class="value">2424</div></div>
        </div>
        <div class="author"><div class="avatar" role="img" aria-label="Member profile photo"></div><div><div class="name">Rovanel</div><div class="when">04/07/2025 · 3:34 PM EST</div></div></div>
        <div class="brand" style="left:214px;top:464px;font-size:11px;gap:5px"><span class="dot" style="width:10px;height:10px"></span>Vantix Pulse</div>
      </article>
      <article class="card card-deep" style="top:537px;height:300px">
        <div class="poster"><div class="big">UNUSUAL</div><div class="sub">OPTIONS ACTIVITY</div></div>
      </article>
    </div>
    <div class="navbar">
      <div class="nav-item" style="left:32px"><svg width="18" height="18" viewBox="0 0 18 18" fill="#fff"><rect x="1" y="1" width="7" height="9"/><rect x="10" y="1" width="7" height="5"/><rect x="1" y="12" width="7" height="5"/><rect x="10" y="8" width="7" height="9"/></svg></div>
      <div class="nav-item" style="left:103px"><svg width="18" height="18" viewBox="0 0 18 18" fill="#fff"><path d="M3 1h9l4 4v12H3z"/><rect x="6" y="8" width="7" height="1.5" fill="#000"/><rect x="6" y="11" width="7" height="1.5" fill="#000"/></svg></div>
      <div class="nav-item active" style="left:190px;width:70px;margin-left:-35px"><svg width="18" height="12" viewBox="0 0 18 12" fill="none" stroke="#4ed07a" stroke-width="2"><path d="M1 11l5-5 3 3 7-7M12 2h4v4"/></svg>Markets</div>
      <div class="nav-item" style="left:278px"><svg width="18" height="18" viewBox="0 0 18 18" fill="#fff"><rect x="2" y="8" width="3.5" height="9"/><rect x="7.5" y="2" width="3.5" height="15"/><rect x="13" y="10" width="3.5" height="7"/></svg></div>
      <div class="nav-item" style="left:348px"><svg width="18" height="18" viewBox="0 0 18 18" fill="#fff"><circle cx="9" cy="5" r="4"/><path d="M1 17c0-5 4-7 8-7s8 2 8 7z"/></svg></div>
    </div>
    <div class="home-bar"></div>
  </section>

  <!-- Screen 3 -->
  <section class="phone" style="left:1037px">
    <div class="status"><span class="clock">7:09 &#9679;</span>
      <svg style="left:270px" width="80" height="14" viewBox="0 0 80 14" fill="#fff"><rect x="0" y="9" width="3" height="4"/><rect x="5" y="6" width="3" height="7"/><rect x="10" y="3" width="3" height="10"/><rect x="15" y="0" width="3" height="13"/><path d="M26 5a10 10 0 0 1 14 0l-2 2a7 7 0 0 0-10 0zM29 8a5 5 0 0 1 8 0l-4 4z"/><rect x="50" y="1" width="23" height="11" rx="3"/><rect x="74" y="4" width="2" height="5" rx="1"/></svg>
    </div>
    <div class="screen-title">Markets</div>
    <nav class="tabs"><span class="tab active" style="left:13px">Option Flow</span><span class="tab" style="left:112px">Darkpool</span><span class="tab" style="left:193px">Treemap</span><span class="tab" style="left:273px">Gamma</span><span class="tab" style="left:346px">Snaps</span></nav>
    <div class="feed">
      <article class="card card-aurora" style="top:19px;height:398px">
        <div class="ticker-badge" style="left:28px;top:28px"><span class="ticker">HVL</span><span class="stamp">04/05/25 | 10:32:12</span></div>
        <div class="trade-type" style="left:28px;top:76px;font-size:38px;line-height:46px">TRADE <span class="side">CALL</span></div>
        <div class="execution" style="left:28px;top:126px">AT ASk</div>
        <div class="stats" style="left:28px;top:162px">
          <div class="stat"><div class="label">STRIKE</div><div class="value">$91</div></div>
          <div class="stat"><div class="label">EXPIRATION</div><div class="value">19 Apr 25</div></div>
          <div class="stat"><div class="label">PREMIUM</div><div class="value">$342.75K</div></div>
          <div class="stat"><div class="label">SIZE@PRICE</div><div class="value">6995@$0.49</div></div>
          <div class="stat"><div class="label">VOLUME</div><div class="value">34.7K</div></div>
          <div class="stat"><div class="label">OPEN INTEREST</div><div class="value">2424</div></div>
        </div>
        <div class="brand" style="left:206px;top:351px;font-size:11px;gap:5px"><span class="dot" style="width:10px;height:10px"></span>Vantix Pulse</div>
      </article>
      <article class="card card-aurora" style="top:439px;height:300px">
        <div class="ticker-badge" style="left:28px;top:28px"><span class="ticker">HVL</span><span class="stamp">04/05/25 | 10:32:12</span></div>
        <div class="trade-type" style="left:28px;top:76px;font-size:38px;line-height:46px">TRADE <span class="side">CALL</span></div>
        <div class="execution" style="left:28px;top:126px">AT ASk</div>
        <div class="stats" style="left:28px;top:162px">
          <div class="stat"><div class="label">STRIKE</div><div class="value">$91</div></div>
          <div class="stat"><div class="label">EXPIRATION</div><div class="value">19 Apr 25</div></div>
        </div>
      </article>
    </div>
    <div class="navbar">
      <div class="nav-item" style="left:32px"><svg width="18" height="18" viewBox="0 0 18 18" fill="#fff"><rect x="1" y="1" width="7" height="9"/><rect x="10" y="1" width="7" height="5"/><rect x="1" y="12" width="7" height="5"/><rect x="10" y="8" width="7" height="9"/></svg></div>
      <div class="nav-item" style="left:103px"><svg width="18" height="18" viewBox="0 0 18 18" fill="#fff"><path d="M3 1h9l4 4v12H3z"/><rect x="6" y="8" width="7" height="1.5" fill="#000"/><rect x="6" y="11" width="7" height="1.5" fill="#000"/></svg></div>
      <div class="nav-item active" style="left:190px;width:70px;margin-left:-35px"><svg width="18" height="12" viewBox="0 0 18 12" fill="none" stroke="#4ed07a" stroke-width="2"><path d="M1 11l5-5 3 3 7-7M12 2h4v4"/></svg>Markets</div>
      <div class="nav-item" style="left:278px"><svg width="18" height="18" viewBox="0 0 18 18" fill="#fff"><rect x="2" y="8" width="3.5" height="9"/><rect x="7.5" y="2" width="3.5" height="15"/><rect x="13" y="10" width="3.5" height="7"/></svg></div>
      <div class="nav-item" style="left:348px"><svg width="18" height="18" viewBox="0 0 18 18" fill="#fff"><circle cx="9" cy="5" r="4"/><path d="M1 17c0-5 4-7 8-7s8 2 8 7z"/></svg></div>
    </div>
    <div class="home-bar"></div>
  </section>

  <!-- Screen 4 -->
  <section class="phone" style="left:1493px">
    <div class="status"><span class="clock">7:09 &#9679;</span>
      <svg style="left:270px" width="80" height="14" viewBox="0 0 80 14" fill="#fff"><rect x="0" y="9" width="3" height="4"/><rect x="5" y="6" width="3" height="7"/><rect x="10" y="3" width="3" height="10"/><rect x="15" y="0" width="3" height="13"/><path d="M26 5a10 10 0 0 1 14 0l-2 2a7 7 0 0 0-10 0zM29 8a5 5 0 0 1 8 0l-4 4z"/><rect x="50" y="1" width="23" height="11" rx="3"/><rect x="74" y="4" width="2" height="5" rx="1"/></svg>
    </div>
    <div class="screen-title">Markets</div>
    <nav class="tabs"><span class="tab active" style="left:13px">Option Flow</span><span class="tab" style="left:112px">Darkpool</span><span class="tab" style="left:193px">Treemap</span><span class="tab" style="left:273px">Gamma</span><span class="tab" style="left:346px">Snaps</span></nav>
    <div class="feed">
      <article class="card card-moss" style="top:32px;height:235px">
        <div class="ticker-badge" style="left:21px;top:21px"><span class="ticker">HVL</span><span class="stamp">04/05/25 | 10:32:12</span></div>
        <div class="trade-type" style="left:21px;top:67px;font-size:18px;line-height:22px;font-weight:800">TRADE <span class="side">CALL</span></div>
        <div class="execution" style="left:197px;top:71px;font-size:12px;line-height:14px">AT ASk</div>
        <div class="mini-stats">
          <div><div class="label">STRIKE</div><div class="value">$91</div></div>
          <div><div class="label">EXPIRATION</div><div class="value">19 Apr 25</div></div>
          <div><div class="label">OPEN INTEREST</div><div class="value">2424</div></div>
          <div><div class="label">PREMIUM</div><div class="value">$342.75K</div></div>
          <div><div class="label">SIZE@PRICE</div><div class="value">6995@$0.49</div></div>
          <div><div class="label">VOLUME</div><div class="value">34.7K</div></div>
        </div>
        <div class="divider" style="left:21px;right:21px;top:180px"></div>
        <div class="brand" style="left:66px;top:196px;font-size:17px"><span class="dot" style="width:22px;height:22px"></span>Vantix Pulse</div>
      </article>
      <article class="card card-moss" style="top:297px;height:235px">
        <div class="ticker-badge bearish" style="left:21px;top:21px"><span class="ticker">HVL</span><span class="stamp">04/05/25 | 10:32:12</span></div>
        <div class="trade-type" style="left:21px;top:67px;font-size:18px;line-height:22px;font-weight:800">TRADE <span class="side">CALL</span></div>
        <div class="execution" style="left:197px;top:71px;font-size:12px;line-height:14px;color:var(--red)">AT ASk</div>
        <div class="mini-stats">
          <div><div class="label">STRIKE</div><div class="value">$91</div></div>
          <div><div class="label">EXPIRATION</div><div class="value">19 Apr 25</div></div>
          <div><div class="label">OPEN INTEREST</div><div class="value">2424</div></div>
          <div><div class="label">PREMIUM</div><div class="value">$342.75K</div></div>
          <div><div class="label">SIZE@PRICE</div><div class="value">6995@$0.49</div></div>
          <div><div class="label">VOLUME</div><div class="value">34.7K</div></div>
        </div>
        <div class="divider" style="left:21px;right:21px;top:180px"></div>
        <div class="brand" style="left:66px;top:196px;font-size:17px"><span class="dot" style="width:22px;height:22px"></span>Vantix Pulse</div>
      </article>
      <article class="card card-moss" style="top:560px;height:235px">
        <div class="ticker-badge" style="left:21px;top:21px"><span class="ticker">HVL</span><span class="stamp">04/05/25 | 10:32:12</span></div>
      </article>
    </div>
    <div class="navbar">
      <div class="nav-item" style="left:32px"><svg width="18" height="18" viewBox="0 0 18 18" fill="#fff"><rect x="1" y="1" width="7" height="9"/><rect x="10" y="1" width="7" height="5"/><rect x="1" y="12" width="7" height="5"/><rect x="10" y="8" width="7" height="9"/></svg></div>
      <div class="nav-item" style="left:103px"><svg width="18" height="18" viewBox="0 0 18 18" fill="#fff"><path d="M3 1h9l4 4v12H3z"/><rect x="6" y="8" width="7" height="1.5" fill="#000"/><rect x="6" y="11" width="7" height="1.5" fill="#000"/></svg></div>
      <div class="nav-item active" style="left:190px;width:70px;margin-left:-35px"><svg width="18" height="12" viewBox="0 0 18 12" fill="none" stroke="#4ed07a" stroke-width="2"><path d="M1 11l5-5 3 3 7-7M12 2h4v4"/></svg>Markets</div>
      <div class="nav-item" style="left:278px"><svg width="18" height="18" viewBox="0 0 18 18" fill="#fff"><rect x="2" y="8" width="3.5" height="9"/><rect x="7.5" y="2" width="3.5" height="15"/><rect x="13" y="10" width="3.5" height="7"/></svg></div>
      <div class="nav-item" style="left:348px"><svg width="18" height="18" viewBox="0 0 18 18" fill="#fff"><circle cx="9" cy="5" r="4"/><path d="M1 17c0-5 4-7 8-7s8 2 8 7z"/></svg></div>
    </div>
    <div class="home-bar"></div>
  </section>

  <h2 class="thanks">Thank you</h2>
  <p class="thanks-note">Your feedback matters to us. Let us<br>know what you think!</p>
</main>
</body>
</html>
```